Animal Eye Clinic needs a Business card

We are a new veterinary ophthalmology practice (Ridgeline Pet Vision Care) and we need a business card designed. We only see animal eyes - we are not a regular veterinary clinic. We already have a logo. We are looking for a professional, good looking business card to hand out to our clients. We are looking for something simple but professional and contemporary. Our logo is likely the only picture/graphic that needs to be on the card.
Updates

Contact Information for Business Card

Delia Vossman, BSc, DVM, MSc, DipACVO
Veterinary Ophthalmologist

Phone: 250.418.3927
Email: ridgelinepetvisioncare@mailbox-example.net
Website: ridgelinepetvisioncare-example.net
Address: 1874 Thornbury Rd
Kelowna, BC, V1X 4M9

Colors

Designer to choose colors to be used in the design.

Requirements
Must have
• Our logo (attached)

```html
<!DOCTYPE html>
<html lang="en">
<head>
<meta charset="utf-8">
<title>Ridgeline Pet Vision Care – Business Card</title>
<link href="https://fonts.googleapis.com/css2?family=Questrial&display=swap" rel="stylesheet">
<style>
  :root {
    --teal: #17929f;
    --grey: #6e6e70;
    --grey-dark: #5f5f61;
    --ink: #4a4a4c;
    --paper: #ffffff;
    --backdrop: #2a2a2b;
  }
  * { margin: 0; padding: 0; box-sizing: border-box; }
  html, body {
    width: 1200px; height: 900px; overflow: hidden;
    background: var(--backdrop);
    font-family: "Questrial", sans-serif;
  }
  .canvas {
    position: relative; width: 1200px; height: 900px;
    display: flex; flex-direction: column; align-items: center; justify-content: center; gap: 36px;
  }
  .card {
    position: relative; width: 700px; height: 400px; border-radius: 18px; overflow: hidden;
  }
  /* Back side */
  .card-back { background: var(--grey); }
  .card-back .brand {
    position: absolute; right: 70px; top: 160px; color: var(--paper);
  }
  /* Brand lockup */
  .brand { display: flex; align-items: center; gap: 14px; }
  .brand-dot { width: 40px; height: 40px; border-radius: 50%; background: currentColor; flex: none; }
  .brand-name { line-height: 1.05; text-transform: uppercase; }
  .brand-name .line-top { display: block; font-size: 15px; letter-spacing: 0.62em; }
  .brand-name .line-main { display: block; font-size: 22px; letter-spacing: 0.02em; }

  /* Front side */
  .card-front { background: var(--paper); }
  .card-front .graphics { position: absolute; inset: 0; }
  .card-front .brand { position: absolute; left: 62px; top: 92px; color: var(--teal); }
  .holder { position: absolute; right: 48px; top: 60px; text-align: right; }
  .holder-name { color: var(--teal); font-size: 30px; letter-spacing: 0.01em; }
  .holder-creds { color: var(--ink); font-size: 13px; margin-top: 4px; }
  .holder-title { color: var(--ink); font-size: 15px; margin-top: 3px; }
  .contact { position: absolute; left: 62px; top: 282px; list-style: none; }
  .contact li {
    display: flex; align-items: center; gap: 9px;
    color: var(--ink); font-size: 14px; line-height: 1; margin-bottom: 10px;
  }
  .contact li.phone { font-size: 17px; }
  .contact .icon { width: 12px; height: 12px; fill: var(--teal); flex: none; }
  .contact .accent { color: var(--teal); }
  .address {
    position: absolute; right: 34px; bottom: 40px; text-align: right;
    color: var(--paper); font-size: 14px; line-height: 1.4;
  }
</style>
</head>
<body>
<main class="canvas">

  <section class="card card-back" aria-label="Card back">
    <div class="brand">
      <span class="brand-dot"></span>
      <span class="brand-name"><span class="line-top">Ridgeline</span><span class="line-main">Pet Vision Care</span></span>
    </div>
  </section>

  <section class="card card-front" aria-label="Card front">
    <svg class="graphics" viewBox="0 0 700 400" aria-hidden="true">
      <line x1="110" y1="265" x2="655" y2="140" stroke="var(--teal)" stroke-width="1.2"/>
      <polygon points="310,400 700,132 700,152 350,400" fill="var(--teal)"/>
      <polygon points="372,400 700,172 700,400" fill="var(--grey)"/>
    </svg>

    <div class="brand">
      <span class="brand-dot"></span>
      <span class="brand-name"><span class="line-top">Ridgeline</span><span class="line-main">Pet Vision Care</span></span>
    </div>

    <div class="holder">
      <p class="holder-name">Delia Vossman</p>
      <p class="holder-creds">BSc, DVM, MSc, DipACVO</p>
      <p class="holder-title">Veterinary Ophthalmologist</p>
    </div>

    <ul class="contact">
      <li class="phone">
        <svg class="icon" viewBox="0 0 24 24"><path d="M6.6 10.8a15.1 15.1 0 0 0 6.6 6.6l2.2-2.2c.3-.3.7-.4 1-.2 1.1.4 2.3.6 3.6.6.6 0 1 .4 1 1V20c0 .6-.4 1-1 1A17 17 0 0 1 3 4c0-.6.4-1 1-1h3.5c.6 0 1 .4 1 1 0 1.3.2 2.5.6 3.6.1.3 0 .7-.2 1z"/></svg>
        250.418.3927
      </li>
      <li>
        <svg class="icon" viewBox="0 0 24 24"><path d="M2 5h20v14H2zm2 2v.5l8 5 8-5V7l-8 5z"/></svg>
        ridgelinepetvisioncare@mailbox-example.net
      </li>
      <li>
        <svg class="icon" viewBox="0 0 24 24"><circle cx="12" cy="12" r="10"/></svg>
        <span>www.<span class="accent">ridgelinepetvisioncare-example.net</span></span>
      </li>
    </ul>

    <p class="address">1874 Thornbury Rd<br>Kelowna, BC, V1X 4M9</p>
  </section>

</main>
</body>
</html>
```